International sourcing and trading company needs website design on Squarespace

We are international sourcing and trading company based in Brisbane ,Australia. We help our clients to source any products they need to economically produce overseas and we manage the whole production process for them. We want our visual identity to show that we are professional, dynamic, efficient and are able to source any product around the world. Our website will be simply information and advertising website , no ecommerce or any transactions. Please see attached our company logo. We would like our website to have the following sections/pages:

1.Main banner with a simple slogan/sentence to introduce what we do: Let us handle the overseas sourcing and production for you.

2. Post-Covid sourcing and producing management: introducing our competence on managing sourcing and overseas production under the travel restriction and the growing tension on global trading. We will supply the exact wording later on;

3. About us: We are a professional team with mature global sourcing and trading experience. We have branch office in Hong Kong and local resources around all areas in China , India and other Asian countries. Our working flow is: received inquiry->start sourcing->(in 1 week time)give price and delivery date on inquired products or further information->(if needed)arrange samples for clients->(if samples and orders are confirmed)deliver Pre-production sample-> kick-off production->arrange inspection through the whole production-> (if need) arrange shipment to client. We would like to show the work flow in a personalized way , eg. personalize icons etc.;

4. What kind of product we can source and produce: our business is sourcing and managing manufacture overseas for our clients, product categories mainly, but not just, are clothing, shoes , bags, clothing accessories, makeup accessories, festival or promotional gifts etc. all kind of daily use products . We basically are able to source and manage production of every kind of products with no limits. We would like this page to be particularly personalized in a way to give impression to whom browse our website feel free to send inquiry of any kind of production to us and they can trust us that we will do our job professionally and dynamically. We are thinking of using some icons of daily use products to show our sourcing category , it's just our though so please feel free to propose any other ides that you think is more suitable from the point of view of professional designer.

5. Start an enquiry: here we need to land on a questionary page to let who would like to make en enquiry leave the main information , including:
-Name & Sir name:
-Company name:
-Contact email:
-Phone numer:
-Enquired product:
-Upload image:
-Preferred or previous production country:
-Preferred price: FOB, CIF, DDP
-If CIF or DDP where the arrival port/airport will be:
-Preferred delivery time:
-Preferred transportation: by air, by sea, by train
- Other specific requires:

6: Contact us: We will supply contact info later on

Above are our thoughts but please feel free to propose any other ideas that you think should be more suitable for us. We trust your expertise and professional opinions.

Wholesalers and retailers who need to produce their products overseas (mainly in China and other countries in Asia)

• We think it will be nice to show information in simple and comprehensive icons instead of piles of words. We will want our website neat, easy to understand what we do and professional. However this is just our thought so please feel free to propose any other ideas that you think is more suitable from the point of view of professional designer.

```html
<!DOCTYPE html>
<html lang="en">
<head>
<meta charset="utf-8">
<title>Harbourline – Global sourcing and trading</title>
<link href="https://fonts.googleapis.com/css2?family=Lato:ital,wght@0,400;0,700;0,900;1,400&display=swap" rel="stylesheet">
<style>
:root{
  --orange:#f5a94a;
  --orange-deep:#f39c2f;
  --teal:#4fb8c9;
  --teal-light:#68c4d1;
  --ink:#1d1d1d;
  --text:#555;
  --footer:#3a3a3a;
  --line:#e6e6e6;
}
*{margin:0;padding:0;box-sizing:border-box}
html,body{width:1200px;height:3028px;overflow:hidden}
body{font-family:'Lato',sans-serif;color:var(--ink);background:#fff;position:relative}
.abs{position:absolute}
/* header */
.site-header{top:0;left:0;width:1200px;height:105px;background:#fff}
.brand{left:110px;top:28px;display:flex;align-items:center;gap:12px}
.brand-dot{width:30px;height:30px;border-radius:50%;background:var(--orange)}
.brand-name{font-size:26px;font-weight:700;color:var(--orange)}
.call{left:857px;top:10px;display:flex;gap:16px;align-items:center}
.call-ring{width:46px;height:46px;border-radius:50%;border:2px solid var(--orange);display:flex;align-items:center;justify-content:center}
.call-label{font-size:12px;font-weight:700}
.call-number{font-size:25px;color:var(--teal);font-weight:700}
.nav{right:110px;top:72px;display:flex;gap:31px;font-size:14px;font-weight:700}
.nav a{color:var(--ink);text-decoration:none}
.nav a.active{color:var(--orange)}
/* hero */
.hero{top:105px;left:0;width:1200px;height:539px;background:linear-gradient(180deg,#c9d3dc 0%,#7d8c8f 30%,#4c6a52 55%,#3f7f80 80%,#356e73 100%)}
.hero h1{position:absolute;top:205px;width:100%;text-align:center;color:#fff;font-size:57px;font-weight:900;line-height:60px;text-shadow:0 2px 8px rgba(0,0,0,.35)}
.dots{right:54px;top:212px;display:flex;flex-direction:column;gap:16px}
.dots span{width:9px;height:9px;border-radius:50%;background:#fff}
.dots span.on{background:none;border:2px solid #fff}
/* about */
.about-art{left:125px;top:715px;width:430px;height:345px;border-radius:50%;background:radial-gradient(circle at 45% 45%,#5aa6c4,#1f4f72 60%,#0f2a44)}
.about-copy{left:657px;top:770px;width:430px}
.section-title{font-size:42px;font-weight:900}
.rule{width:40px;height:3px;background:var(--teal);margin:20px 0 26px}
.about-copy p{font-size:16.5px;line-height:34.5px;color:var(--text)}
.flow-heading{top:1093px;left:0;width:1200px;text-align:center;font-size:16px;font-style:italic;font-weight:700;color:var(--teal);text-decoration:underline}
.flow{top:1146px;left:110px;display:flex;align-items:center}
.step{width:106px;height:106px;border-radius:50%;border:2px dashed var(--orange);display:flex;align-items:center;justify-content:center}
.step.alt{border-color:var(--teal)}
.step-inner{width:94px;height:94px;border-radius:50%;background:var(--teal);color:#fff;display:flex;flex-direction:column;align-items:center;justify-content:center;text-align:center;font-size:12px;font-weight:700;line-height:14px}
.step.alt .step-inner{background:var(--orange)}
.step-inner small{font-size:9px}
.step-inner svg{margin-bottom:4px}
.arrow{width:17px;display:flex;justify-content:center}
/* covid */
.covid{top:1360px;left:0;width:1200px;height:212px;background:linear-gradient(90deg,#f2b462,#f5ad55 50%,#f3b565);color:#fff;text-align:center}
.covid h2{margin-top:50px;font-size:28px;font-weight:900}
.covid p{margin:18px auto 0;width:830px;font-size:18px;font-style:italic;line-height:28px}
/* products */
.products-title{top:1645px;left:0;width:1200px;text-align:center}
.products-title .rule{margin:20px auto 0}
.tabs{top:1770px;left:107px;display:flex;gap:8.5px}
.tab{width:134px;height:86px;background:#fff;box-shadow:0 1px 6px rgba(0,0,0,.12);display:flex;flex-direction:column;align-items:center;justify-content:center;color:var(--teal);font-size:14px;font-weight:700;text-align:center;line-height:17px;gap:6px}
.tab.active{background:var(--teal);color:#fff}
.cards{top:1930px;left:103px;display:flex;gap:21px}
.card{width:233px;height:272px;box-shadow:0 1px 6px rgba(0,0,0,.14);text-align:center;padding-top:16px}
.card-img{width:110px;height:110px;margin:0 auto;border-radius:10px}
.card h3{margin-top:28px;font-size:14px;font-weight:700}
.card p{margin-top:10px;font-size:14px;line-height:26px;color:var(--text);padding:0 16px}
/* enquiry */
.enquiry{top:2328px;left:0;width:1200px;height:320px;background:linear-gradient(180deg,#6ac5d2,#5fbccb);text-align:center;color:#fff}
.enquiry h2{margin-top:42px;font-size:44px;font-weight:900}
.enquiry .rule{background:#fff;margin:14px auto 26px}
.enquiry p{font-size:14px;line-height:28px}
.btn{display:inline-flex;align-items:center;gap:10px;margin-top:22px;padding:0 14px;height:48px;background:var(--orange-deep);color:#fff;font-size:15px;font-weight:700}
.btn i{width:14px;height:14px;border-radius:50%;background:#fff;display:inline-block}
/* footer */
.footer{top:2648px;left:0;width:1200px;height:380px;background:var(--footer);color:#fff}
.f-brand{left:112px;top:84px;font-size:26px;font-weight:700;display:flex;gap:10px;align-items:center}
.f-brand span{width:26px;height:26px;border-radius:50%;background:#fff}
.f-about{left:112px;top:142px;width:312px;font-size:14px;line-height:26px;text-align:justify}
.socials{left:112px;top:232px;display:flex;gap:8px}
.socials span{width:33px;height:33px;border-radius:50%;border:2px solid #fff}
.f-head{font-size:14px;font-weight:700;text-decoration:underline}
.contact{left:470px;top:78px}
.contact-row{display:flex;align-items:center;gap:24px;font-size:14px;line-height:20px}
.icon-circ{width:30px;height:30px;border-radius:50%;border:1.5px solid #fff;display:flex;align-items:center;justify-content:center}
.links{font-size:14px}
.links li{list-style:none;margin-top:13px;display:flex;gap:14px}
.links li::before{content:"»"}
.divider{left:112px;top:307px;width:975px;height:1px;background:#888}
.copy{top:330px;left:0;width:1200px;text-align:center;font-size:14px}
</style>
</head>
<body>

<header class="abs site-header">
  <div class="abs brand"><span class="brand-dot"></span><span class="brand-name">Harbourline</span></div>
  <div class="abs call">
    <div class="call-ring"><svg width="20" height="20" viewBox="0 0 24 24"><path d="M6.6 10.8c1.4 2.8 3.8 5.1 6.6 6.6l2.2-2.2c.3-.3.7-.4 1-.2 1.1.4 2.3.6 3.6.6.6 0 1 .4 1 1V20c0 .6-.4 1-1 1C10.6 21 3 13.4 3 4c0-.6.4-1 1-1h3.5c.6 0 1 .4 1 1 0 1.3.2 2.5.6 3.6.1.3 0 .7-.2 1L6.6 10.8z" fill="none" stroke="#4fb8c9" stroke-width="1.6"/></svg></div>
    <div><div class="call-label">CALL US TODAY</div><div class="call-number">1 800 555 0142</div></div>
  </div>
  <nav class="abs nav">
    <a class="active">HOME</a><a>ABOUT US</a><a>OUR PRODUCTS</a><a>LATEST NEWS</a><a>REVIEWS</a><a>CONTACT US</a>
  </nav>
</header>

<section class="abs hero" role="img" aria-label="Aerial photo of a harbour city skyline">
  <h1>Let us handle the overseas<br>sourcing &amp; production for you.</h1>
  <div class="abs dots"><span></span><span></span><span class="on"></span><span></span><span></span></div>
</section>

<div class="abs about-art" role="img" aria-label="Globe illustration wrapped in arrow bands"></div>
<div class="abs about-copy">
  <h2 class="section-title">About Us</h2>
  <div class="rule"></div>
  <p>We are a professional team with mature global sourcing and trading experience. We have branch office in Hong Kong and local resources around all areas in China , India and other Asian countries.</p>
</div>

<div class="abs flow-heading">OUR WORKING FLOW</div>
<div class="abs flow">
  <div class="step alt"><div class="step-inner"><svg width="22" height="26"><rect x="2" y="2" width="18" height="22" rx="2" fill="none" stroke="#fff" stroke-width="2"/></svg>RECEIVED<br>INQUIRY</div></div>
  <div class="arrow"><svg width="12" height="12"><path d="M2 2l6 4-6 4" fill="none" stroke="#f5a94a" stroke-width="2"/></svg></div>
  <div class="step"><div class="step-inner" style="background:var(--orange)"><svg width="24" height="24"><circle cx="10" cy="10" r="7" fill="none" stroke="#fff" stroke-width="2"/><path d="M15 15l6 6" stroke="#fff" stroke-width="2"/></svg>START<br>SOURCING</div></div>
  <div class="arrow"><svg width="12" height="12"><path d="M2 2l6 4-6 4" fill="none" stroke="#4fb8c9" stroke-width="2"/></svg></div>
  <div class="step alt"><div class="step-inner" style="background:var(--teal)"><svg width="24" height="24"><circle cx="12" cy="12" r="9" fill="none" stroke="#fff" stroke-width="2"/><path d="M8 16l8-8" stroke="#fff" stroke-width="2"/></svg>GIVE<br>PRICE</div></div>
  <div class="arrow"><svg width="12" height="12"><path d="M2 2l6 4-6 4" fill="none" stroke="#f5a94a" stroke-width="2"/></svg></div>
  <div class="step alt"><div class="step-inner" style="background:var(--orange)"><svg width="24" height="24"><rect x="3" y="3" width="18" height="18" fill="none" stroke="#fff" stroke-width="2"/></svg>ARRANGE<br>SAMPLES</div></div>
  <div class="arrow"><svg width="12" height="12"><path d="M2 2l6 4-6 4" fill="none" stroke="#4fb8c9" stroke-width="2"/></svg></div>
  <div class="step"><div class="step-inner"><svg width="24" height="24"><path d="M4 20h16M8 20V8h8v12" fill="none" stroke="#fff" stroke-width="2"/></svg>DELIVER<br><small>PRODUCTION</small></div></div>
  <div class="arrow"><svg width="12" height="12"><path d="M2 2l6 4-6 4" fill="none" stroke="#f5a94a" stroke-width="2"/></svg></div>
  <div class="step alt"><div class="step-inner" style="background:var(--orange)"><svg width="24" height="24"><circle cx="12" cy="12" r="8" fill="none" stroke="#fff" stroke-width="2"/><circle cx="12" cy="12" r="3" fill="#fff"/></svg>KICK-OFF<br><small>PRODUCTION</small></div></div>
  <div class="arrow"><svg width="12" height="12"><path d="M2 2l6 4-6 4" fill="none" stroke="#4fb8c9" stroke-width="2"/></svg></div>
  <div class="step"><div class="step-inner"><svg width="24" height="24"><circle cx="11" cy="11" r="7" fill="none" stroke="#fff" stroke-width="2"/><path d="M8 11l2 2 4-4" fill="none" stroke="#fff" stroke-width="2"/></svg>ARRANGE<br>INSPECTION</div></div>
  <div class="arrow"><svg width="12" height="12"><path d="M2 2l6 4-6 4" fill="none" stroke="#f5a94a" stroke-width="2"/></svg></div>
  <div class="step alt"><div class="step-inner" style="background:var(--orange)"><svg width="26" height="22"><rect x="2" y="6" width="15" height="11" fill="none" stroke="#fff" stroke-width="2"/><path d="M17 10h5l2 4v3h-7" fill="none" stroke="#fff" stroke-width="2"/></svg>ARRANGE<br>SHIPMENT</div></div>
</div>

<section class="abs covid" role="img" aria-label="Orange-tinted photo of business people in an office">
  <h2>POST - COVID SOURCING &amp; PRODUCING MANAGEMENT</h2>
  <p>Introducing our competence on managing sourcing and overseas production under the travel restriction and the growing tension on global trading. We will supply the exact wording later on</p>
</section>

<div class="abs products-title"><h2 class="section-title">Our Products</h2><div class="rule"></div></div>
<div class="abs tabs">
  <div class="tab"><svg width="30" height="30"><rect x="2" y="2" width="26" height="26" fill="none" stroke="#4fb8c9" stroke-width="2"/><path d="M15 2v26M2 15h26" stroke="#4fb8c9" stroke-width="2"/></svg>ALL</div>
  <div class="tab"><svg width="34" height="28"><path d="M10 3l-8 6 4 4 3-2v15h16V11l3 2 4-4-8-6h-4a4 4 0 0 1-6 0z" fill="none" stroke="#f5a94a" stroke-width="1.6"/></svg>CLOTHING</div>
  <div class="tab"><svg width="50" height="24"><path d="M3 18c0-6 6-12 14-12l8 6c8 1 20 2 22 8v2H3z" fill="none" stroke="#4fb8c9" stroke-width="1.6"/></svg>SHOES</div>
  <div class="tab active"><svg width="26" height="30"><rect x="3" y="9" width="20" height="19" rx="2" fill="none" stroke="#fff" stroke-width="1.6"/><path d="M8 9V6a5 5 0 0 1 10 0v3" fill="none" stroke="#fff" stroke-width="1.6"/></svg>BAGS</div>
  <div class="tab"><svg width="32" height="30"><rect x="3" y="10" width="26" height="18" fill="none" stroke="#f5a94a" stroke-width="1.6"/><path d="M11 10V4h10v6" fill="none" stroke="#f5a94a" stroke-width="1.6"/></svg>CLOTHING<br>ACCESSORIES</div>
  <div class="tab"><svg width="40" height="24"><rect x="3" y="5" width="28" height="16" rx="6" fill="none" stroke="#f5a94a" stroke-width="1.6"/><circle cx="17" cy="13" r="3" fill="none" stroke="#f5a94a" stroke-width="1.6"/><rect x="33" y="6" width="4" height="15" fill="none" stroke="#f5a94a" stroke-width="1.6"/></svg>MAKEUP<br>ACCESSORIES</div>
  <div class="tab"><svg width="30" height="30"><rect x="3" y="11" width="24" height="17" fill="none" stroke="#f5a94a" stroke-width="1.6"/><path d="M15 11v17M3 16h24M15 11c-4-8-10-4-6 0M15 11c4-8 10-4 6 0" fill="none" stroke="#f5a94a" stroke-width="1.6"/></svg>PROMOTIONAL<br>GIFTS</div>
</div>

<div class="abs cards">
  <div class="card"><div class="card-img" role="img" aria-label="Tan leather shoulder bag" style="background:#c99a6c"></div><h3>PRODUCT TITLE</h3><p>Lorem ipsum dolor sit amet, consectetur adipiscing elit, sed do eiusmod tempor incidid</p></div>
  <div class="card"><div class="card-img" role="img" aria-label="Pink handbag" style="background:#f1b9c2"></div><h3>PRODUCT TITLE</h3><p>Lorem ipsum dolor sit amet, consectetur adipiscing elit, sed do eiusmod tempor incidid</p></div>
  <div class="card"><div class="card-img" role="img" aria-label="Orange tote bag" style="background:#d98a4e"></div><h3>PRODUCT TITLE</h3><p>Lorem ipsum dolor sit amet, consectetur adipiscing elit, sed do eiusmod tempor incidid</p></div>
  <div class="card"><div class="card-img" role="img" aria-label="Orange saddle bag" style="background:#ee8a3a"></div><h3>PRODUCT TITLE</h3><p>Lorem ipsum dolor sit amet, consectetur adipiscing elit, sed do eiusmod tempor incidid</p></div>
</div>

<section class="abs enquiry" role="img" aria-label="Teal-tinted background of aircraft over a world map">
  <h2>Start An Enquiry</h2>
  <div class="rule"></div>
  <p>here we need to land on a questionary page to let who would like to make<br>en enquiry leave the main information</p>
  <span class="btn">ENQUIRY NOW <i></i></span>
</section>

<footer class="abs footer">
  <div class="abs f-brand"><span></span>Harbourline</div>
  <p class="abs f-about">Lorem ipsum dolor sit amet, consectetur adipiscing elit, sed do eiusmod tempor incididunt ut labore et dolore magna aliqua.</p>
  <div class="abs socials"><span></span><span></span><span></span><span></span></div>

  <div class="abs contact">
    <div class="f-head">CONTACT US</div>
    <div class="contact-row" style="margin-top:24px"><div class="icon-circ"><svg width="14" height="16"><path d="M7 15s5-5 5-9A5 5 0 0 0 2 6c0 4 5 9 5 9z" fill="none" stroke="#fff" stroke-width="1.4"/><circle cx="7" cy="6" r="1.8" fill="#fff"/></svg></div><div>124 , Lorem Ipsum Dolor<br>United States</div></div>
    <div class="contact-row" style="margin-top:34px"><div class="icon-circ"><svg width="14" height="12"><rect x="1" y="1" width="12" height="10" fill="none" stroke="#fff" stroke-width="1.4"/><path d="M1 1l6 5 6-5" fill="none" stroke="#fff" stroke-width="1.4"/></svg></div><div>info@harbourline.example</div></div>
    <div class="contact-row" style="margin-top:30px"><div class="icon-circ"><svg width="14" height="14" viewBox="0 0 24 24"><path d="M6.6 10.8c1.4 2.8 3.8 5.1 6.6 6.6l2.2-2.2c.3-.3.7-.4 1-.2 1.1.4 2.3.6 3.6.6.6 0 1 .4 1 1V20c0 .6-.4 1-1 1C10.6 21 3 13.4 3 4c0-.6.4-1 1-1h3.5c.6 0 1 .4 1 1 0 1.3.2 2.5.6 3.6.1.3 0 .7-.2 1z" fill="none" stroke="#fff" stroke-width="2"/></svg></div><div style="font-size:20px;font-weight:700">1 800 555 0142</div></div>
  </div>

  <div class="abs links" style="left:779px;top:78px">
    <div class="f-head">QUICK LINKS</div>
    <ul><li>Home</li><li>About Us</li><li>Our Products</li><li>Latest News</li><li>Reviews</li></ul>
  </div>
  <div class="abs links" style="left:950px;top:78px">
    <div class="f-head">OTHER LINKS</div>
    <ul><li>Contact Us</li><li>FAQ</li><li>Help Service</li><li>Terms Of Use</li><li>Privacy Policy</li></ul>
  </div>

  <div class="abs divider"></div>
  <div class="abs copy">© 2020 Harbourline. All Rights Reserved</div>
</footer>

</body>
</html>
```